brovlanepass.net

Develop a website for brolanepass.net will be a site to sell tickets for concerts, shows, shows, theaters and others. I need a web design easy view, very easy to use and accumulate events by date. The aim is to develop the site was connected to a complex system that is already developed. (Important this page to a robust system was connected via links the idea is to develop only the front view)
Updates

Reason: I need more designs yet we have not made the decision

Target Market(s)

millennials, adults, who want to enjoy concerts and shows

Industry/Entity Type

Event

Number of Pages Required

5+ page

Colors
1b1b1b
aaaaaa
ffffff

Requirements
Must have
• Easy Vista, accumulation of upcoming events, past events. The tabs should have are: 1 Start: In this part of upcoming events occur. You could put a banner on the top and down the events by date. 2. How to order: page with instructions on how to purchase tickets 3. About Us: The company history 4. Contact: Phones and template for contact by mail 5. Our policies: shopping 6. Notice Privacy: Privacy Notice Copoy 7. Centers Sale: physical places where they can purchase tickets Promoters 8. access: Link to a template
Nice to have
• as you can see p www.quimbarostage.net or farunda.net or farunda.org or gallowmerk.net (important this page to a robust system was connected via links the idea is to develop only the front view)
Should not have
• Many things Tangled

```html
<!DOCTYPE html>
<html lang="en">
<head>
<meta charset="utf-8">
<title>Contact Us – Brovlane Pass</title>
<link rel="stylesheet" href="https://fonts.googleapis.com/css2?family=Montserrat:wght@700;800&family=Open+Sans:wght@300;400;600&family=Roboto:wght@400&family=Jost:wght@400&display=swap">
<style>
:root{
  --black:#000;
  --ink:#1b1b1b;
  --grey:#aaaaaa;
  --white:#fff;
  --panel:#e6e6e6;
  --field:#fff;
  --accent:#e8544f;
  --label:#333;
  --nav-top:#2a2a2a;
  --nav-bottom:#111;
  --plum:#2a0a1c;
  --night:#0e0b14;
}
*{box-sizing:border-box;margin:0;padding:0}
html,body{width:1031px;height:1200px;overflow:hidden;background:var(--black)}
body{position:relative;font-family:"Open Sans",sans-serif;color:var(--white)}
.abs{position:absolute}

/* Header */
.topbar{left:0;top:0;width:1031px;height:96px;background:var(--black)}
.phone{left:90px;top:30px;display:flex;align-items:center;gap:11px;font-family:"Roboto",sans-serif;font-size:19px}
.phone-ring{width:37px;height:37px;border:1.5px solid var(--white);border-radius:50%;display:flex;align-items:center;justify-content:center}
.brand{display:flex;align-items:center;gap:8px;font-family:"Open Sans",sans-serif;font-weight:600;color:var(--white);letter-spacing:.5px}
.brand-mark{width:12px;height:12px;background:var(--accent)}
.brand--header{left:0;width:1031px;top:34px;justify-content:center;font-size:22px}
.social{display:flex;gap:11px}
.social span{width:20px;height:20px;border-radius:3px;display:block}
.social--header{left:828px;top:37px}
.social--header span{background:#1a9ad6}

/* Navigation */
.nav{left:0;top:96px;width:1031px;height:50px;background:linear-gradient(var(--nav-top),var(--nav-bottom));border-top:1px solid #333}
.nav a{position:absolute;top:0;height:50px;line-height:50px;font-size:14px;color:var(--white);text-decoration:none;font-family:"Open Sans",sans-serif}
.nav a.active{background:var(--black);border-top:3px solid var(--accent);line-height:44px;padding:0 14px}

/* Hero */
.hero{left:0;top:146px;width:1031px;height:154px;background:radial-gradient(ellipse at 75% 40%,#4a4450 0%,#2a252c 40%,#141214 100%)}
.hero h1{position:absolute;left:0;width:1031px;top:70px;text-align:center;font-family:"Montserrat",sans-serif;font-weight:800;font-size:31px;letter-spacing:.5px}

/* Main */
.main{left:0;top:300px;width:1031px;height:650px;background:radial-gradient(ellipse at 30% 60%,#3a0c26 0%,var(--plum) 35%,var(--night) 90%)}
.section-title{left:76px;top:358px;font-size:26px;font-weight:300}
.form-panel{left:78px;top:410px;width:429px;height:462px;background:var(--panel)}
.form-label{position:absolute;left:34px;font-size:13px;color:var(--label)}
.field{position:absolute;left:32px;width:365px;height:43px;background:var(--field);border:1px solid #d2d2d2;box-shadow:0 1px 2px rgba(0,0,0,.12)}
.submit{position:absolute;left:36px;top:396px;width:104px;height:30px;border-radius:15px;background:var(--accent);color:var(--white);font-size:13px;display:flex;align-items:center;justify-content:center}
.info-title{left:544px;top:404px;font-size:23px}
.info-text{left:545px;top:440px;width:415px;font-size:11.6px;line-height:20.4px;text-align:justify}
.contact-list{left:543px;top:587px;font-size:13.5px;line-height:25.6px;list-style:none}
.contact-list li{display:flex;align-items:center;gap:7px}
.contact-list svg{width:11px;height:11px;flex:none}
.map{left:543px;top:687px;width:412px;height:184px;background:linear-gradient(135deg,#dcdcdc,#cfcfcf 60%,#d8d8d8)}

/* Footer */
.footer{left:0;top:950px;width:1031px;height:250px;background:var(--black)}
.brand--footer{left:77px;top:1046px;font-size:19px}
.footer-head{font-family:"Jost",sans-serif;font-size:14px;text-transform:uppercase;top:1000px}
.footer-contact{left:296px;top:1032px;font-size:11.5px;line-height:19px}
.footer-note{left:552px;top:1031px;width:180px;font-size:10.5px;line-height:14px}
.subscribe{left:552px;top:1067px;display:flex}
.subscribe .email{width:126px;height:26px;background:var(--white);color:#777;font-size:10px;padding:7px 7px}
.subscribe .go{width:48px;height:26px;background:#4a4a4a;font-size:10.5px;display:flex;align-items:center;justify-content:center}
.social--footer{left:809px;top:1038px}
.social--footer span{width:22px;height:22px;background:var(--white);margin-right:0}
.rule{left:65px;top:1143px;width:879px;height:1px;background:#333}
.copyright{left:0;width:1031px;top:1163px;text-align:center;font-size:11.5px}
</style>
</head>
<body>

<header class="abs topbar">
  <div class="abs phone">
    <div class="phone-ring">
      <svg width="16" height="16" viewBox="0 0 24 24"><path fill="#fff" d="M6.6 10.8a15.2 15.2 0 0 0 6.6 6.6l2.2-2.2a1 1 0 0 1 1-.25 11.4 11.4 0 0 0 3.6.57 1 1 0 0 1 1 1V20a1 1 0 0 1-1 1A17 17 0 0 1 3 4a1 1 0 0 1 1-1h3.5a1 1 0 0 1 1 1c0 1.25.2 2.45.57 3.57a1 1 0 0 1-.25 1z"/></svg>
    </div>
    <span>+852 5550 1287</span>
  </div>
  <div class="abs brand brand--header"><span class="brand-mark"></span>BROVLANE PASS</div>
  <div class="abs social social--header" aria-label="Social links"><span></span><span></span><span></span><span></span></div>
</header>

<nav class="abs nav">
  <a style="left:104px">HOME</a>
  <a style="left:187px">HOW TO ORDER</a>
  <a style="left:332px">ABOUT US</a>
  <a class="active" style="left:426px">CONTACT US</a>
  <a style="left:565px">POLICIES</a>
  <a style="left:664px">PRIVACY</a>
  <a style="left:759px">CENTER SALE</a>
  <a style="left:885px">ACCESS</a>
</nav>

<section class="abs hero" role="img" aria-label="Concert hall audience facing a lit stage">
  <h1>CONTACT US</h1>
</section>

<main class="abs main"></main>
<h2 class="abs section-title">Contact Form</h2>

<form class="abs form-panel">
  <label class="form-label" style="top:30px">Name (required)</label>
  <div class="field" style="top:50px"></div>
  <label class="form-label" style="top:112px">Phone Number (required)</label>
  <div class="field" style="top:132px"></div>
  <label class="form-label" style="top:193px">Email (required)</label>
  <div class="field" style="top:215px"></div>
  <label class="form-label" style="top:275px">Message (required)</label>
  <div class="field" style="top:296px;height:86px;left:34px"></div>
  <div class="submit">SUBMIT</div>
</form>

<h3 class="abs info-title">Brovlane Pass</h3>
<p class="abs info-text">It is a long established fact that a reader will be distracted by the readable content of a page when looking at its layout. The point of using Lorem Ipsum is that it has a more-or-less normal distribution of letters, as opposed to using 'Content here, content here', making it look like readable English. Many desktop publishing packages and web page editors now use Lorem Ipsum as their default model text, and a search for 'lorem ipsum' will uncover many web sites still in their infancy</p>

<ul class="abs contact-list">
  <li><svg viewBox="0 0 24 24"><path fill="#fff" d="M12 2a7 7 0 0 0-7 7c0 5 7 13 7 13s7-8 7-13a7 7 0 0 0-7-7zm0 9.5A2.5 2.5 0 1 1 12 6.5a2.5 2.5 0 0 1 0 5z"/></svg>412 Calder Row Westfield, Fl, 33090</li>
  <li><svg viewBox="0 0 24 24"><path fill="#fff" d="M6.6 10.8a15.2 15.2 0 0 0 6.6 6.6l2.2-2.2a1 1 0 0 1 1-.25 11.4 11.4 0 0 0 3.6.57 1 1 0 0 1 1 1V20a1 1 0 0 1-1 1A17 17 0 0 1 3 4a1 1 0 0 1 1-1h3.5a1 1 0 0 1 1 1c0 1.25.2 2.45.57 3.57a1 1 0 0 1-.25 1z"/></svg>555-210-4470 | Fax: 555-210-4471</li>
  <li><svg viewBox="0 0 24 24"><path fill="#fff" d="M2 5h20v14H2z"/><path fill="none" stroke="#1a0a14" stroke-width="2" d="M2 5l10 8 10-8"/></svg>hello@brovlanepass.net</li>
</ul>

<div class="abs map" role="img" aria-label="Street map showing the office location"></div>

<footer class="abs footer"></footer>
<div class="abs brand brand--footer"><span class="brand-mark"></span>BROVLANE PASS</div>

<h4 class="abs footer-head" style="left:295px">Contact Us</h4>
<p class="abs footer-contact">Address : 412 Calder Row,<br>Westfield, Fl, 33090<br>Phone : 555-210-4470<br>Email : hello@brovlanepass.net</p>

<h4 class="abs footer-head" style="left:552px">Join Our Mailing List</h4>
<p class="abs footer-note">Your about us information would fit here nicely.</p>
<div class="abs subscribe"><div class="email">Email address</div><div class="go">Submit</div></div>

<h4 class="abs footer-head" style="left:809px">Follow Us Out There</h4>
<div class="abs social social--footer" aria-label="Social links"><span></span><span></span><span></span><span></span></div>

<div class="abs rule"></div>
<p class="abs copyright">Copyright © 2017. All Rights Reserved</p>

</body>
</html>
```